Vitamin B12 Liquid Drops Label

hi, i need a label designed for my vitamin b12 drops that i am going to be selling on shopzello. the label needs to quickly capture the attention of a buyer as he or she is scrolling through the thumbnail search results on shopzello.com my brand is called nralo. i already have an example brand logo i will be using, however, i need help designing the rest of the label. attached are some examples of labels i like for other supplements.some of these examples are pink. i do not want pink. please go for a blue/green color scheme. THE DESIGN MUST BE BOLD

Target Market(s)

adults ages 30 - 64

Font styles to use
Sans Serif

Colors
0455a3
cedeed
3176b5
85acd3
cfdeed
9bcb3b
abd037
cadf82
00a990

Requirements
Must have
• - bold design
• - somewhat gender-neutral color scheme because this will be used equally by men and women
• - B12 MUST be very prominent and visible on the label
Should not have
• - it should not be "crunchy" looking

```html
<!DOCTYPE html>
<html lang="en">
<head>
<meta charset="utf-8">
<title>Nralo Vitamin B12 Drops Label</title>
<link href="https://fonts.googleapis.com/css2?family=Source+Sans+3:wght@700;800&display=swap" rel="stylesheet">
<style>
  :root {
    --backdrop: #cedeed;
    --label-green: #9bcb3b;
    --label-blue: #0455a3;
    --ink-blue: #0455a3;
    --ink-green: #cadf82;
  }
  html, body {
    margin: 0;
    padding: 0;
    width: 1200px;
    height: 900px;
    overflow: hidden;
    background: var(--backdrop);
  }
  .canvas {
    position: relative;
    width: 1200px;
    height: 900px;
    background: var(--backdrop);
  }
  .label {
    position: absolute;
    left: 320px;
    top: 96px;
    width: 560px;
    height: 709px;
    font-family: "Source Sans 3", "Segoe UI", sans-serif;
    box-shadow: 0 18px 40px rgba(4, 50, 100, 0.22);
  }
  .label-panels {
    position: absolute;
    inset: 0;
    width: 100%;
    height: 100%;
    display: block;
  }
  .product-name {
    position: absolute;
    left: 16px;
    top: 306px;
    margin: 0;
    font-size: 70px;
    font-weight: 800;
    line-height: 1;
    letter-spacing: 0.01em;
    color: var(--ink-blue);
    white-space: nowrap;
  }
  .product-form {
    position: absolute;
    left: 26px;
    top: 398px;
    margin: 0;
    font-size: 22px;
    font-weight: 700;
    line-height: 1;
    letter-spacing: 0.44em;
    color: var(--ink-green);
    white-space: nowrap;
  }
  .brand-name {
    position: absolute;
    right: 28px;
    bottom: 44px;
    margin: 0;
    font-size: 68px;
    font-weight: 800;
    line-height: 1;
    color: var(--ink-green);
  }
</style>
</head>
<body>
  <main class="canvas">
    <section class="label" aria-label="Vitamin B12 drops label">
      <svg class="label-panels" viewBox="0 0 560 709" preserveAspectRatio="none" aria-hidden="true">
        <rect class="panel-green" x="0" y="0" width="560" height="709" fill="var(--label-green)"/>
        <polygon class="panel-blue" points="560,0 420,372 0,372 0,709 560,709" fill="var(--label-blue)"/>
      </svg>
      <h1 class="product-name">VITAMIN B12</h1>
      <p class="product-form">METHYLCOBAMALIN</p>
      <p class="brand-name">NRALO</p>
    </section>
  </main>
</body>
</html>
```